Onboarding Carousel UI/UX design

We need a great UI/UX design for our onboarding carousel as attached in the PDF document. The chosen designers will be given our brand book with colors and styles to be used. The images must be focused on the content of each slide and be professional unique style (Do not use the childish cartoons we have used for placeholders)

Industry/Entity Type

Mortgage Brokerage

Number of Pages Required

5+ page

Font styles to use
Other font styles liked:
• Roboto

Requirements
Must have
• Great UI / UX design
Very relevant content of the images to match the slide
Nice to have
• Brand book

https://pv.lumorak.com/view/ed991dda-3474-4c3e-9747-882e21ba3df5-b8ca/?fullscreen

Image styles we like. Would need to be customized and made unique for us.

https://pinvarlo.com/shots/6300615-Torvane-Quillet-Illustration-Collaboration
https://meltridgestudio.co.za/software-client-style-frames
Should not have
• Do not use the childish images we have used as placeholders

```html
<!DOCTYPE html>
<html lang="en">
<head>
<meta charset="utf-8">
<title>Lendory Partners – Onboarding Carousel</title>
<link href="https://fonts.googleapis.com/css2?family=Roboto:wght@400;500&display=swap" rel="stylesheet">
<style>
  :root {
    --stage: #1e1e1e;
    --panel-top: #f3f5f9;
    --panel-bottom: #d3dbe9;
    --title: #1d1d1d;
    --accent: #a3124f;
    --body-blue: #1f3f8f;
    --small: #333740;
    --dot: #a9bcdb;
    --dot-active: #0f347a;
    --bar: #f1f3f8;
    --go: #6b7d0a;
    --go-text: #ffffff;
  }
  * { box-sizing: border-box; margin: 0; padding: 0; }
  html, body { width: 1188px; height: 1200px; overflow: hidden; background: var(--stage); }
  body { position: relative; font-family: "Roboto", sans-serif; }

  .slide {
    position: absolute; width: 274px; height: 558px; overflow: hidden;
    background: linear-gradient(180deg, var(--panel-top) 0%, var(--panel-bottom) 100%);
  }
  .slide__brand { position: absolute; top: 8px; left: 0; right: 0; text-align: center; white-space: nowrap;
    font-size: 27px; font-weight: 400; color: var(--title); letter-spacing: 0.2px; }
  .slide__art { position: absolute; left: 18px; top: 58px; width: 238px; height: 208px; border-radius: 44% 56% 48% 52%; }
  .slide__heading { position: absolute; top: 295px; left: 8px; right: 8px; text-align: center;
    font-size: 17px; line-height: 21.5px; font-weight: 500; color: var(--accent); }
  .slide__lead { position: absolute; top: 349px; left: 12px; right: 12px; text-align: center;
    font-size: 10.4px; line-height: 16px; color: var(--body-blue); }
  .slide__note { position: absolute; top: 384px; left: 10px; right: 10px; text-align: center;
    font-size: 6.4px; line-height: 12px; color: var(--small); }
  .slide__note--low { top: 400px; }

  .dots { position: absolute; top: 445px; left: 0; right: 0; display: flex; justify-content: center; gap: 11.4px; }
  .dots span { width: 10px; height: 10px; border-radius: 50%; background: var(--dot); }
  .dots span.is-active { background: var(--dot-active); }

  .actions { position: absolute; top: 502px; left: 13px; right: 13px; height: 34px; background: var(--bar); }
  .actions__account { position: absolute; left: 10px; top: 6px; font-size: 9.6px; color: var(--title); }
  .actions__account a { display: block; margin-top: 3px; font-size: 7.4px; color: var(--body-blue); text-decoration: none; }
  .btn-next { position: absolute; right: 5px; top: 4px; width: 60px; height: 26px; background: var(--go);
    color: var(--go-text); font-size: 12.4px; font-weight: 500; display: flex; align-items: center; justify-content: center; gap: 5px; }
  .btn-next svg { width: 12px; height: 12px; }
  .btn-start { position: absolute; top: 502px; left: 13px; right: 13px; height: 34px; background: var(--go);
    color: var(--go-text); font-size: 12.4px; font-weight: 500; display: flex; align-items: center; justify-content: center; }

  .slide__code { position: absolute; right: 4px; bottom: 3px; font-size: 5px; color: var(--small); }

  .feature__title { position: absolute; font-size: 14.6px; line-height: 21.5px; font-weight: 500; color: var(--accent); }
  .feature__text { position: absolute; font-size: 10.4px; line-height: 16.3px; color: var(--body-blue); }
  .feature__art { position: absolute; border-radius: 14px; }
  .right { text-align: right; }
</style>
</head>
<body>

<!-- Welcome -->
<section class="slide" style="left:32px; top:38px;">
  <h1 class="slide__brand">Lendory Partners</h1>
  <div class="slide__art" role="img" aria-label="Illustration of a house on a tablet with coins, charts and two people" style="background: linear-gradient(145deg,#dce7f7,#9ab6e6 55%,#3c62b4);"></div>
  <h2 class="slide__heading">Welcome to Lendory Partners<br>Apply Online</h2>
  <p class="slide__lead">You can apply online for your next mortgage credit in about 20 minutes.</p>
  <p class="slide__note">It's easy, and we will guide you all the way.<br>See the five simple steps that you have to take!</p>
  <div class="dots"><span class="is-active"></span><span></span><span></span><span></span><span></span><span></span><span></span></div>
  <div class="actions">
    <div class="actions__account">Already have an account?<a href="#">Logon</a></div>
    <div class="btn-next">Next <svg viewBox="0 0 12 12"><circle cx="6" cy="6" r="5.2" fill="none" stroke="#fff" stroke-width="1"/><path d="M5 3.6 7.4 6 5 8.4" fill="none" stroke="#fff" stroke-width="1.1"/></svg></div>
  </div>
  <span class="slide__code">M2</span>
</section>

<!-- Step 1 -->
<section class="slide" style="left:315px; top:38px;">
  <h1 class="slide__brand">Lendory Partners</h1>
  <div class="slide__art" role="img" aria-label="Illustration of an open envelope with an at sign, a phone and people around it" style="background: linear-gradient(150deg,#c9d3f5,#8fa1ea 50%,#e5645c);"></div>
  <h2 class="slide__heading">#1 Create your personal<br>account</h2>
  <p class="slide__lead">You will need a valid email address to create your account</p>
  <p class="slide__note">We will send you a confirmation email, make sure you click the link to verify your email address.</p>
  <div class="dots"><span></span><span class="is-active"></span><span></span><span></span><span></span><span></span><span></span></div>
  <div class="actions">
    <div class="btn-next">Next <svg viewBox="0 0 12 12"><circle cx="6" cy="6" r="5.2" fill="none" stroke="#fff" stroke-width="1"/><path d="M5 3.6 7.4 6 5 8.4" fill="none" stroke="#fff" stroke-width="1.1"/></svg></div>
  </div>
  <span class="slide__code">M2</span>
</section>

<!-- Step 2 -->
<section class="slide" style="left:598px; top:38px;">
  <h1 class="slide__brand">Lendory Partners</h1>
  <div class="slide__art" role="img" aria-label="Illustration of a smartphone with chat bubbles between two people" style="background: linear-gradient(150deg,#d9dde3,#1f9e7a 55%,#1c3f8f);"></div>
  <h2 class="slide__heading">#2 Secure your account with<br>your mobile phone</h2>
  <p class="slide__lead">You will need a valid mobile phone number to enable two factor authentication.</p>
  <p class="slide__note">We will send you an SMS containing a security code to verify your mobile number.</p>
  <div class="dots"><span></span><span></span><span class="is-active"></span><span></span><span></span><span></span><span></span></div>
  <div class="actions">
    <div class="btn-next">Next <svg viewBox="0 0 12 12"><circle cx="6" cy="6" r="5.2" fill="none" stroke="#fff" stroke-width="1"/><path d="M5 3.6 7.4 6 5 8.4" fill="none" stroke="#fff" stroke-width="1.1"/></svg></div>
  </div>
  <span class="slide__code">M2</span>
</section>

<!-- Step 3 -->
<section class="slide" style="left:881px; top:38px;">
  <h1 class="slide__brand">Lendory Partners</h1>
  <div class="slide__art" role="img" aria-label="Illustration of a monitor showing an identity profile with a tick" style="background: linear-gradient(180deg,#dfe7f5,#b4c7e8 60%,#232a3a); border-radius:10px; left:48px; width:178px; top:96px; height:148px;"></div>
  <h2 class="slide__heading">#3 Verify your identity<br>online</h2>
  <p class="slide__lead">You will need to have a valid Romanian ID card or residence permit</p>
  <p class="slide__note">From your smart phone, you will take a photo of your card and make a selfie video.</p>
  <div class="dots"><span></span><span></span><span></span><span class="is-active"></span><span></span><span></span><span></span></div>
  <div class="actions">
    <div class="btn-next">Next <svg viewBox="0 0 12 12"><circle cx="6" cy="6" r="5.2" fill="none" stroke="#fff" stroke-width="1"/><path d="M5 3.6 7.4 6 5 8.4" fill="none" stroke="#fff" stroke-width="1.1"/></svg></div>
  </div>
  <span class="slide__code">M2</span>
</section>

<!-- Step 4 -->
<section class="slide" style="left:174px; top:604px;">
  <h1 class="slide__brand">Lendory Partners</h1>
  <div class="slide__art" role="img" aria-label="Illustration of two people beside a large phone showing a checklist" style="background: linear-gradient(160deg,#d7e8f6,#8fc0e8 50%,#3e78c9);"></div>
  <h2 class="slide__heading">#4 Create your profile data for<br>the application</h2>
  <p class="slide__lead">Tell us about your current situation including employment, income, assets and liabilities</p>
  <p class="slide__note">It is essential to have everything as accurate as possible so you can be presented with the right offers</p>
  <div class="dots"><span></span><span></span><span></span><span></span><span class="is-active"></span><span></span><span></span></div>
  <div class="actions">
    <div class="btn-next">Next <svg viewBox="0 0 12 12"><circle cx="6" cy="6" r="5.2" fill="none" stroke="#fff" stroke-width="1"/><path d="M5 3.6 7.4 6 5 8.4" fill="none" stroke="#fff" stroke-width="1.1"/></svg></div>
  </div>
  <span class="slide__code">M2</span>
</section>

<!-- Step 5 -->
<section class="slide" style="left:457px; top:604px;">
  <h1 class="slide__brand">Lendory Partners</h1>
  <div class="slide__art" role="img" aria-label="Illustration of a money tree, growing bar chart and people with coins" style="background: linear-gradient(150deg,#ecdcf3,#c58be0 50%,#7a1f86); top:96px; height:150px;"></div>
  <h2 class="slide__heading">#5 Apply for the right loan for<br>your needs</h2>
  <p class="slide__lead">You will be presented with your options, upload any supporting documents and then submit your application online.</p>
  <p class="slide__note slide__note--low">Then we take it from here to get your approval.</p>
  <div class="dots"><span></span><span></span><span></span><span></span><span></span><span class="is-active"></span><span></span></div>
  <div class="actions">
    <div class="btn-next">Next <svg viewBox="0 0 12 12"><circle cx="6" cy="6" r="5.2" fill="none" stroke="#fff" stroke-width="1"/><path d="M5 3.6 7.4 6 5 8.4" fill="none" stroke="#fff" stroke-width="1.1"/></svg></div>
  </div>
  <span class="slide__code">M2</span>
</section>

<!-- Benefits -->
<section class="slide" style="left:740px; top:604px;">
  <h1 class="slide__brand">Lendory Partners</h1>

  <h2 class="feature__title" style="left:13px; top:69px;">Our service is<br>100% free</h2>
  <p class="feature__text" style="left:13px; top:115px; width:125px;">The banks pay us a com-<br>mission, so you don't have<br>too.</p>
  <div class="feature__art" role="img" aria-label="Illustration of a wallet with falling coins" style="left:178px; top:72px; width:48px; height:76px; background: linear-gradient(180deg,#f1e6c4,#a8683a);"></div>

  <div class="feature__art" role="img" aria-label="Illustration of a support agent on a laptop screen" style="left:9px; top:204px; width:115px; height:84px; background: linear-gradient(150deg,#bcd3ec,#2c3f9a 60%,#e04a6a);"></div>
  <h2 class="feature__title right" style="right:13px; top:197px;">Team of experts<br>here to help you</h2>
  <p class="feature__text right" style="right:13px; top:244px; width:130px;">Our mortgage experts stay by your side the whole way, keeping you in the loop.</p>

  <h2 class="feature__title" style="left:13px; top:334px;">Made in Romania<br>with love</h2>
  <p class="feature__text" style="left:13px; top:380px; width:125px;">We love to help peopleand would love to haveyou as our customer</p>
  <div class="feature__art" role="img" aria-label="Illustration of a person holding a large red heart" style="left:194px; top:320px; width:67px; height:120px; background: linear-gradient(180deg,#e2503f 0%,#e2503f 45%,#173c7a 100%); border-radius:30px 30px 18px 18px;"></div>

  <div class="dots" style="top:466px;"><span></span><span></span><span></span><span></span><span></span><span></span><span class="is-active"></span></div>
  <div class="btn-start">Get Started</div>
  <span class="slide__code">M2</span>
</section>

</body>
</html>
```